Design a poster that illustrates the six central pillars of our school district's efforts with students. The attached PDF outlines the six main competencies we aim for students to possess upon graduation. Each of the 6 has 3 bullet points for the poster as well. The title is "Profile of a Trailblazer". Our mascot is this attached winged wheel. The overall concept is that staff take kids when they are young and develop these 6 things when they graduate. Our colors are navy, red, and white. We will make this poster in a variety of sizes in offices, classrooms, and in digital spaces as well. On the PDF - ignore the column that says "Synthesis". That has nothing to do with this poster.

The district is Harlow Creek Public Schools https://www.harlowcreek-schools.example/

```html
<!DOCTYPE html>
<html lang="en">
<head>
<meta charset="utf-8">
<title>Profile of a Trailblazer – Harlow Creek Public Schools</title>
<link href="https://fonts.googleapis.com/css2?family=League+Gothic&family=Montserrat:wght@500&family=Arimo:wght@400;700&display=swap" rel="stylesheet">
<style>
  :root {
    --navy: #1f2c48;
    --red: #a01c25;
    --white: #ffffff;
    --backdrop: #d3d3d3;
  }
  * { box-sizing: border-box; margin: 0; padding: 0; }
  html, body { width: 1200px; height: 814px; overflow: hidden; }
  body { background: var(--backdrop); position: relative; }

  .poster {
    position: absolute; left: 330px; top: 26px;
    width: 539px; height: 762px;
    background: var(--navy);
    overflow: hidden;
    box-shadow: 0 4px 14px rgba(0,0,0,.25);
  }

  /* Header */
  .title-accent { position: absolute; left: 0; top: 20px; width: 56px; height: 89px; background: var(--red); }
  .title-band { position: absolute; left: 33px; top: 28px; width: 506px; height: 72px; background: var(--white); }
  .poster-title {
    position: absolute; left: 60px; top: 32px; height: 64px;
    font-family: "League Gothic", "Oswald", sans-serif;
    font-weight: 400; font-size: 60px; line-height: 64px;
    color: var(--red); letter-spacing: .3px; white-space: nowrap;
  }

  /* Pillar columns */
  .pillar-column {
    position: absolute; top: 142px;
    display: flex; flex-direction: column; gap: 34px;
  }
  .col-left  { left: 33px;  width: 214px; }
  .col-right { left: 281px; width: 215px; }

  .pillar {
    position: relative;
    border: 1.5px solid var(--white);
    padding: 26px 10px 8px 15px;
  }
  .pillar-head {
    position: absolute; top: -19px; left: -8px;
    height: 38px; padding: 0 8px 0 0;
    display: flex; align-items: center; gap: 12px;
    background: var(--navy);
  }
  .pillar-icon { width: 30px; height: 30px; flex: none; }
  .pillar-name {
    font-family: "League Gothic", "Oswald", sans-serif;
    font-weight: 400;
    font-size: 38px; line-height: 38px; color: var(--white);
    white-space: nowrap;
  }
  .traits { list-style: none; }
  .trait {
    position: relative;
    font-family: "Montserrat", sans-serif; font-weight: 500;
    font-size: 10px; line-height: 12px; color: var(--white);
    margin-bottom: 10px;
  }
  .trait:last-child { margin-bottom: 0; }
  .trait::before {
    content: ""; position: absolute; left: -21px; top: 1px;
    width: 9px; height: 9px; background: var(--navy);
    border: 1px solid var(--white);
  }
  .trait::after {
    content: ""; position: absolute; left: -19px; top: 3px;
    width: 5px; height: 5px; background: var(--red);
  }
  .trait .tick {
    position: absolute; left: -18px; top: 1.5px;
    width: 3px; height: 6px;
    border-right: 1.5px solid var(--white); border-bottom: 1.5px solid var(--white);
    transform: rotate(40deg); z-index: 1;
  }

  /* Footer */
  .footer-band { position: absolute; left: 0; top: 680px; width: 539px; height: 61px; background: var(--red); }
  .footer-light { position: absolute; left: 0; top: 696px; width: 130px; height: 45px; background: var(--white); }
  .footer-rule { position: absolute; left: 0; top: 741px; width: 539px; height: 4px; background: var(--white); }
  .district-mark {
    position: absolute; left: 92px; top: 678px; width: 56px; height: 56px;
    border-radius: 50%; background: var(--white); border: 3px solid var(--navy);
  }
  .district-name {
    position: absolute; left: 184px; top: 690px;
    font-family: "Arimo", Arial, sans-serif; font-weight: 700;
    font-size: 20px; line-height: 22px; color: var(--white); white-space: nowrap;
  }
  .district-motto {
    position: absolute; left: 184px; top: 713px;
    font-family: "Arimo", Arial, sans-serif; font-weight: 400;
    font-size: 16.5px; line-height: 20px; color: var(--white); white-space: nowrap;
  }
</style>
</head>
<body>
<main class="poster">
  <div class="title-accent"></div>
  <div class="title-band"></div>
  <h1 class="poster-title">PROFILE OF A TRAILBLAZER</h1>

  <div class="pillar-column col-left">
    <section class="pillar">
      <div class="pillar-head">
        <svg class="pillar-icon" viewBox="0 0 30 30" aria-hidden="true">
          <rect x="9" y="3" width="19" height="13" rx="2" fill="#fff"/>
          <rect x="2" y="11" width="18" height="12" rx="2" fill="#fff" stroke="#1f2c48" stroke-width="1.5"/>
          <path d="M5 22 L4 28 L10 23Z" fill="#fff"/>
          <circle cx="7" cy="17" r="1.3" fill="#1f2c48"/><circle cx="11" cy="17" r="1.3" fill="#1f2c48"/><circle cx="15" cy="17" r="1.3" fill="#1f2c48"/>
        </svg>
        <h2 class="pillar-name">Communicator</h2>
      </div>
      <ul class="traits">
        <li class="trait"><span class="tick"></span>Expresses ideas clearly and respectfully (written &amp; verbal).</li>
        <li class="trait"><span class="tick"></span>Listens actively and understands diverse perspectives.</li>
        <li class="trait"><span class="tick"></span>Adjusts communication to suit the audience and context.</li>
      </ul>
    </section>

    <section class="pillar">
      <div class="pillar-head">
        <svg class="pillar-icon" viewBox="0 0 30 30" aria-hidden="true">
          <circle cx="15" cy="11" r="7" fill="none" stroke="#fff" stroke-width="2.2"/>
          <rect x="12" y="18" width="6" height="4" fill="#fff"/>
          <path d="M6 23 Q15 30 24 23" fill="none" stroke="#fff" stroke-width="2.2"/>
          <path d="M15 1v2M5 11H3M27 11h-2M8 4l1.5 1.5M22 4l-1.5 1.5" stroke="#fff" stroke-width="1.6"/>
        </svg>
        <h2 class="pillar-name">Critical Thinker</h2>
      </div>
      <ul class="traits">
        <li class="trait"><span class="tick"></span>Questions, analyzes, and evaluates information from multiple sources.</li>
        <li class="trait"><span class="tick"></span>Identifies and solves complex problems creatively.</li>
        <li class="trait"><span class="tick"></span>Uses evidence and diverse perspectives to form reasoned conclusions and make informed decisions.</li>
      </ul>
    </section>

    <section class="pillar">
      <div class="pillar-head">
        <svg class="pillar-icon" viewBox="0 0 30 30" aria-hidden="true">
          <circle cx="9" cy="6" r="2.5" fill="#fff"/><circle cx="15" cy="4.5" r="2.8" fill="#fff"/><circle cx="21" cy="6" r="2.5" fill="#fff"/>
          <path d="M5 14 Q9 8 13 14Z M11 13 Q15 6 19 13Z M17 14 Q21 8 25 14Z" fill="#fff"/>
          <rect x="1" y="19" width="4" height="9" fill="#fff"/>
          <path d="M6 20 L14 19 Q17 20 16 22 L11 22 M6 27 L18 27 L28 20 Q27 18 25 19 L19 22" fill="none" stroke="#fff" stroke-width="2"/>
        </svg>
        <h2 class="pillar-name">Responsible</h2>
      </div>
      <ul class="traits">
        <li class="trait"><span class="tick"></span>Takes ownership of actions, choices, and commitments.</li>
        <li class="trait"><span class="tick"></span>Manages time, resources, and self to meet expectations.</li>
        <li class="trait"><span class="tick"></span>Acts with integrity and advocates for self and others.</li>
      </ul>
    </section>
  </div>

  <div class="pillar-column col-right">
    <section class="pillar">
      <div class="pillar-head">
        <svg class="pillar-icon" viewBox="0 0 30 30" aria-hidden="true">
          <rect x="4" y="3" width="7" height="7" fill="#fff"/>
          <circle cx="24" cy="14" r="4" fill="#fff"/>
          <path d="M9 27 L13 20 L17 27Z" fill="#fff"/>
          <path d="M16 3 Q22 3 23 8 M22 24 Q18 28 14 27 M4 20 Q2 15 5 12" fill="none" stroke="#fff" stroke-width="1.6"/>
        </svg>
        <h2 class="pillar-name">Adaptable</h2>
      </div>
      <ul class="traits">
        <li class="trait"><span class="tick"></span>Responds productively to new situations, challenges, and feedback.</li>
        <li class="trait"><span class="tick"></span>Learns from new experiences and applies prior knowledge in evolving contexts.</li>
        <li class="trait"><span class="tick"></span>Adjusts behavior and approach to effectively engage with diverse groups and environments.</li>
      </ul>
    </section>

    <section class="pillar">
      <div class="pillar-head">
        <svg class="pillar-icon" viewBox="0 0 30 30" aria-hidden="true">
          <rect x="3" y="10" width="10" height="10" fill="#fff"/>
          <rect x="14" y="6" width="11" height="11" fill="#fff"/>
          <rect x="5" y="21" width="7" height="7" fill="#fff"/>
          <circle cx="13.5" cy="15" r="2.2" fill="#fff"/><circle cx="19.5" cy="17.5" r="2" fill="#1f2c48"/>
        </svg>
        <h2 class="pillar-name">Collaborator</h2>
      </div>
      <ul class="traits">
        <li class="trait"><span class="tick"></span>Contributes effectively and cooperatively to shared goals.</li>
        <li class="trait"><span class="tick"></span>Listens actively and values diverse ideas and perspectives.</li>
        <li class="trait"><span class="tick"></span>Engages respectfully, compromising and leading when appropriate.</li>
      </ul>
    </section>

    <section class="pillar">
      <div class="pillar-head">
        <svg class="pillar-icon" viewBox="0 0 30 30" aria-hidden="true">
          <path d="M15 20 L8 13 Q5 9 9 7 Q13 6 15 10 Q17 6 21 7 Q25 9 22 13Z" fill="#fff"/>
          <path d="M2 14 L8 22 L12 28 M28 14 L22 22 L18 28" fill="none" stroke="#fff" stroke-width="2.4"/>
          <path d="M15 1v3M9 3l1 2M21 3l-1 2" stroke="#fff" stroke-width="1.4"/>
        </svg>
        <h2 class="pillar-name">Compassionate</h2>
      </div>
      <ul class="traits">
        <li class="trait"><span class="tick"></span>Understands and acknowledges others' feelings, perspectives, and experiences.</li>
        <li class="trait"><span class="tick"></span>Responds with kindness, patience, and support.</li>
        <li class="trait"><span class="tick"></span>Seeks to connect with and contribute positively to the well-being of others and the community.</li>
      </ul>
    </section>
  </div>

  <div class="footer-band"></div>
  <div class="footer-light"></div>
  <div class="footer-rule"></div>
  <div class="district-mark"></div>
  <p class="district-name">Harlow Creek Public Schools</p>
  <p class="district-motto">Excellence in Academics, Arts &amp; Athletics</p>
</main>
</body>
</html>
```